Fresh, modern, fun business card for pediatric dental practice

Need a business card for fresh, modern, fun pediatric dental practice

Clean look that matches our website's font and colors

We prefer the look of curved corners on business cards

Target Market(s)

parents (mothers) of young children, professionals, mid-high class

Industry/Entity Type

Dental

Contact Information for Business Card

Maplebrook Pediatric Dentistry
482 Quarry Lane
Suite 517
Ashvale, PA 17599
717.555.0193
www.maplebrookkidsdental.example

Mei-Ran Tsai, DMD
Corinne Walbeck, DMD
(we are working on our email address, but we would like that on the card as well)

Font styles to use
Sans Serif

Requirements
Must have
• All info; we would also like to make cards for individual staff members
• colors from our website and color palatte, attatched
• use same font and design as website for branding
Nice to have
• clean, simple card that has a pop of color
• we would like to see a few designs with our tag line "where smiles get brighter"
• we are not sure if we want to have it on there or not
• we would like to see a few designs incorporating the ribbon graphic on our website where the word WELCOME is

```html
<!DOCTYPE html>
<html lang="en">
<head>
<meta charset="utf-8">
<title>Maplebrook Pediatric Dentistry – Business Cards</title>
<link href="https://fonts.googleapis.com/css2?family=Roboto:wght@500&family=Lato:wght@400;700&family=Open+Sans:wght@600&display=swap" rel="stylesheet">
<style>
  :root {
    --magenta: #d0288e;
    --magenta-deep: #c8248a;
    --orange: #f7a21b;
    --ink: #4a4a4a;
    --paper: #ffffff;
    --paper-fade: #f1f1f1;
    --backdrop: #3d3d3d;
  }
  * { margin: 0; padding: 0; box-sizing: border-box; }
  html, body { width: 1200px; height: 960px; overflow: hidden; }
  body { background: var(--backdrop); position: relative; }

  .card {
    position: absolute;
    width: 475px;
    height: 268px;
    border-radius: 12px;
    box-shadow: 0 4px 10px rgba(0,0,0,.45);
    overflow: hidden;
  }
  .card--front {
    left: 110px;
    background: linear-gradient(180deg, var(--paper) 55%, var(--paper-fade) 100%);
    text-align: center;
  }
  .card--back { left: 611px; background: var(--magenta); }
  .card--row1 { top: 184px; }
  .card--row2 { top: 502px; }

  .name-ribbon {
    position: absolute;
    left: 100px;
    top: 46px;
    width: 276px;
    height: 37px;
  }
  .name-ribbon svg { position: absolute; inset: 0; }
  .name-ribbon__text {
    position: relative;
    line-height: 37px;
    font-family: "Roboto", sans-serif;
    font-weight: 500;
    font-size: 19px;
    color: #fff;
    letter-spacing: -0.2px;
  }
  .name-ribbon__title { color: var(--orange); }

  .practice {
    position: absolute;
    left: 0; right: 0;
    top: 115px;
    font-family: "Lato", sans-serif;
    font-style: normal;
    font-size: 11px;
    line-height: 15px;
    color: var(--ink);
  }
  .practice__name { color: var(--magenta); font-weight: 700; }

  .contact-icons {
    position: absolute;
    left: 0; right: 0;
    top: 177px;
    display: flex;
    justify-content: center;
    gap: 4px;
  }
  .contact-icons svg { width: 13px; height: 13px; }

  .contact {
    position: absolute;
    left: 0; right: 0;
    top: 193px;
    font-family: "Lato", sans-serif;
    font-size: 11px;
    line-height: 17px;
    color: var(--ink);
  }

  .brand {
    position: absolute;
    left: 0; right: 0;
    text-align: center;
    font-family: "Open Sans", sans-serif;
    font-weight: 600;
    color: #fff;
  }
  .brand__dot {
    display: block;
    width: 30px; height: 30px;
    margin: 0 auto 12px;
    border-radius: 50%;
    background: #fff;
  }
  .brand__name { font-size: 30px; line-height: 34px; letter-spacing: 1px; }
  .brand__sub { font-size: 17px; line-height: 20px; letter-spacing: 1.5px; }
  .card--row1 .brand { top: 93px; }

  .pattern-field {
    position: absolute;
    inset: 0;
    background: linear-gradient(135deg, var(--magenta) 0%, var(--magenta-deep) 100%);
  }
  .card--row2 .brand { top: 110px; }
  .card--row2 .brand__name { font-size: 26px; line-height: 30px; }
  .card--row2 .brand__sub { font-size: 14px; line-height: 18px; }
</style>
</head>
<body>

<svg width="0" height="0" style="position:absolute">
  <defs>
    <g id="icon-phone">
      <circle cx="8" cy="8" r="8" fill="#d0288e"/>
      <path d="M5.2 4.2l1.4-.3 1 2.1-.9.7c.5 1.1 1.3 1.9 2.4 2.4l.7-.9 2.1 1-.3 1.4c-3.5.2-6.6-2.9-6.4-6.4z" fill="#fff"/>
    </g>
    <g id="icon-mail">
      <circle cx="8" cy="8" r="8" fill="#d0288e"/>
      <rect x="4" y="5.2" width="8" height="5.6" rx=".6" fill="#fff"/>
      <path d="M4.3 5.6L8 8.3l3.7-2.7" fill="none" stroke="#d0288e" stroke-width=".9"/>
    </g>
    <g id="icon-web">
      <circle cx="8" cy="8" r="8" fill="#d0288e"/>
      <circle cx="8" cy="8" r="4" fill="none" stroke="#fff" stroke-width="1"/>
      <ellipse cx="8" cy="8" rx="1.7" ry="4" fill="none" stroke="#fff" stroke-width=".9"/>
      <path d="M4 8h8" stroke="#fff" stroke-width=".9"/>
    </g>
    <polygon id="ribbon-shape" points="0,0 276,0 262,18.5 276,37 0,37 14,18.5" fill="#d0288e"/>
  </defs>
</svg>

<section class="card card--front card--row1">
  <div class="name-ribbon">
    <svg viewBox="0 0 276 37"><use href="#ribbon-shape"/></svg>
    <p class="name-ribbon__text">Mei-Ran Tsai, <span class="name-ribbon__title">DMD</span></p>
  </div>
  <address class="practice">
    <span class="practice__name">Maplebrook Pediatric Dentistry</span><br>
    482 Quarry Lane, Suite 517<br>
    Ashvale, PA 17599
  </address>
  <div class="contact-icons">
    <svg viewBox="0 0 16 16"><use href="#icon-phone"/></svg>
    <svg viewBox="0 0 16 16"><use href="#icon-mail"/></svg>
    <svg viewBox="0 0 16 16"><use href="#icon-web"/></svg>
  </div>
  <p class="contact">717.555.0193<br>info@maplebrookkidsdental.example<br>www.maplebrookkidsdental.example</p>
</section>

<section class="card card--back card--row1">
  <div class="brand">
    <span class="brand__dot"></span>
    <div class="brand__name">Maplebrook</div>
    <div class="brand__sub">Pediatric Dentistry</div>
  </div>
</section>

<section class="card card--front card--row2">
  <div class="name-ribbon">
    <svg viewBox="0 0 276 37"><use href="#ribbon-shape"/></svg>
    <p class="name-ribbon__text">Corinne Walbeck, <span class="name-ribbon__title">DMD</span></p>
  </div>
  <address class="practice">
    <span class="practice__name">Maplebrook Pediatric Dentistry</span><br>
    482 Quarry Lane, Suite 517<br>
    Ashvale, PA 17599
  </address>
  <div class="contact-icons">
    <svg viewBox="0 0 16 16"><use href="#icon-phone"/></svg>
    <svg viewBox="0 0 16 16"><use href="#icon-mail"/></svg>
    <svg viewBox="0 0 16 16"><use href="#icon-web"/></svg>
  </div>
  <p class="contact">717.555.0193<br>info@maplebrookkidsdental.example<br>www.maplebrookkidsdental.example</p>
</section>

<section class="card card--back card--row2">
  <div class="pattern-field" role="img" aria-label="Repeating pattern of orange sun motifs on magenta"></div>
  <div class="brand">
    <div class="brand__name">Maplebrook</div>
    <div class="brand__sub">Pediatric Dentistry</div>
  </div>
</section>

</body>
</html>
```